HearthMile business card and stationary design

We are looking for a simple yet elegant design for our mortgage company business card and stationary.

The card should include:
Name (Marcus Pell)
Title (CEO)
Phone Number (732-555-0182)
Address (48 Birchwell Court, Suite 314, Hazlet, NJ 07730)
Email (email@hearthmile.example)
"NMLS" i.e. (NMLS 61947)
"Company NMLS" (Company NMLS 274615)

Contact Information for Business Card

See above

```html
<!DOCTYPE html>
<html lang="en">
<head>
<meta charset="utf-8">
<title>HearthMile Business Card</title>
<link href="https://fonts.googleapis.com/css2?family=Montserrat:wght@500;700&family=Arimo:wght@400;700&display=swap" rel="stylesheet">
<style>
  :root {
    --navy: #192632;
    --sky: #03adea;
    --paper: #ffffff;
    --backdrop: #9a9a9a;
  }
  * { margin: 0; padding: 0; box-sizing: border-box; }
  html, body {
    width: 1093px;
    height: 1200px;
    overflow: hidden;
  }
  body {
    position: relative;
    background: var(--backdrop);
    font-family: "Arimo", Arial, sans-serif;
  }
  .card {
    position: absolute;
    left: 264px;
    width: 580px;
    height: 357px;
    overflow: hidden;
  }
  .card--front { top: 226px; background: var(--paper); }
  .card--back  { top: 620px; background: var(--navy); }

  .wordmark {
    position: absolute;
    left: 0;
    right: 0;
    text-align: center;
    font-family: "Montserrat", Arial, sans-serif;
    font-weight: 500;
    font-size: 58px;
    line-height: 1;
    letter-spacing: 0.5px;
  }
  .card--front .wordmark { top: 84px; color: var(--navy); }
  .card--back .wordmark  { top: 150px; color: var(--paper); }

  .details {
    position: absolute;
    left: 0;
    top: 180px;
    width: 100%;
    height: 131px;
    background: var(--navy);
    color: var(--paper);
  }
  .person {
    position: absolute;
    left: 26px;
    top: 10px;
  }
  .person__name {
    font-family: "Montserrat", Arial, sans-serif;
    font-weight: 700;
    font-size: 24px;
    line-height: 1.1;
    color: var(--sky);
  }
  .person__title {
    font-size: 16px;
    line-height: 1.2;
    margin-top: 2px;
  }
  .licences {
    margin-top: 10px;
    font-size: 16px;
    line-height: 21px;
  }
  .label { color: var(--sky); }
  .contact {
    position: absolute;
    left: 355px;
    top: 52px;
    font-size: 16px;
    line-height: 21px;
  }
  .contact .label { font-weight: 700; margin-right: 4px; }

  .address-bar {
    position: absolute;
    left: 0;
    bottom: 0;
    width: 100%;
    height: 46px;
    background: var(--sky);
    color: var(--paper);
    font-size: 16px;
    display: flex;
    align-items: center;
    justify-content: center;
    gap: 5px;
    padding-bottom: 4px;
  }
  .address-bar svg { width: 12px; height: 17px; }
</style>
</head>
<body>
  <section class="card card--front">
    <div class="wordmark">HearthMile</div>

    <div class="details">
      <div class="person">
        <div class="person__name">Marcus Pell</div>
        <div class="person__title">CEO</div>
        <div class="licences">
          <div><span class="label">NMLS</span> 61947</div>
          <div><span class="label">Company NMLS</span> 274615</div>
        </div>
      </div>
      <div class="contact">
        <div><span class="label">T:</span>732-555-0182</div>
        <div><span class="label">E:</span>email@hearthmile.example</div>
        <div><span class="label">W:</span>www.hearthmile.example</div>
      </div>
    </div>

    <div class="address-bar">
      <svg viewBox="0 0 12 17" aria-hidden="true">
        <path d="M6 0C2.7 0 0 2.6 0 5.9 0 10.2 6 17 6 17s6-6.8 6-11.1C12 2.6 9.3 0 6 0zm0 8.3a2.4 2.4 0 1 1 0-4.8 2.4 2.4 0 0 1 0 4.8z" fill="#ffffff"/>
      </svg>
      <span>48 Birchwell Court, Suite 314, Larkfield, NJ 08219</span>
    </div>
  </section>

  <section class="card card--back">
    <div class="wordmark">HearthMile</div>
  </section>
</body>
</html>
```